Modern business card design for professional copywriter

I'd like a business card design that I can use to have my cards printed out by quillprint.com as a squared corners business card (see artwork and design guidelines here: https://help.quillprint.com/hc/en-gb/sections/200570950-QUILL-Product-Templates)

The design should be clean and modern and reflect the colours, tone and branding on my website: https://tessavorrin.com.au

Target Market(s)

Professionals, B2B small business owners

Industry/Entity Type

Business

Contact Information for Business Card

Tessa Vorrin
m: 0468 905 327
e: tessa@tessavorrin.com.au
w: tessavorrin.com.au

Font styles to use
Sans Serif

Requirements
Must have
• Tagline: "Smart copywriting for clever business people"
• Brand colours: fd8000, 009984, 666666 and black
Nice to have

```html
<!DOCTYPE html>
<html lang="en">
<head>
<meta charset="utf-8">
<title>Tessa Vorrin – Business Card</title>
<link rel="stylesheet" href="https://fonts.googleapis.com/css2?family=Montserrat:wght@500;600;700&display=swap">
<style>
  :root {
    --brand-teal: #009984;
    --brand-teal-soft: #1a9e88;
    --paper: #ffffff;
    --text-light: #ffffff;
    --edge-grey: #d9d9d9;
  }
  html, body {
    margin: 0;
    padding: 0;
    width: 1200px;
    height: 805px;
    overflow: hidden;
    background: var(--paper);
  }
  .card {
    position: relative;
    width: 1200px;
    height: 805px;
    background: var(--paper);
    font-family: "Montserrat", Arial, sans-serif;
  }
  .card-face {
    position: absolute;
    left: 28px;
    top: 28px;
    width: 1154px;
    height: 686px;
    background: var(--brand-teal-soft);
    border-right: 4px solid var(--edge-grey);
  }
  .brand-lockup {
    position: absolute;
    left: 0;
    right: 0;
    top: 360px;
    transform: translateY(-50%);
    text-align: center;
    color: var(--text-light);
  }
  .brand-name {
    margin: 0;
    font-size: 84px;
    font-weight: 700;
    letter-spacing: -1px;
    line-height: 1;
  }
  .brand-role {
    margin: 10px 0 0 270px;
    font-size: 24px;
    font-weight: 600;
    letter-spacing: 8px;
    line-height: 1;
  }
  .tagline {
    position: absolute;
    left: 0;
    right: 0;
    top: 736px;
    margin: 0;
    text-align: center;
    color: var(--brand-teal);
    font-size: 27px;
    font-weight: 500;
    text-transform: uppercase;
    letter-spacing: 0.2px;
  }
</style>
</head>
<body>
  <main class="card">
    <section class="card-face">
      <div class="brand-lockup">
        <h1 class="brand-name">Tessa Vorrin</h1>
        <p class="brand-role">COPYWRITER</p>
      </div>
    </section>
    <p class="tagline">Smart copywriting for clever business people</p>
  </main>
</body>
</html>
```